Automotive spring company needs banner for website

Banner dimensions: 3840 x 880 pixels
Banner need to be consistent with our branding (logo, stationary, colors, fonts, message).
People images should show happiness and it is preferable those people are in or around a car unless it ties into one of the 3 quotes in the must haves below.
Use color blue #4885ed
and gold color #f7d105
Minimal, strong, clean, & tech

35-55 male and female

Auto Repair

• Clickable element for "Shop" or "Make an Appointment"
• "25 Years of Customer Satisfaction" or
• "Get it Done Right by Specialist" or
• "Peace of Mind National Warranty"
• Use our font, Eurostile and/or complimentary font paring

```html
<!DOCTYPE html>
<html lang="en">
<head>
<meta charset="utf-8">
<title>Coilhaus Web Banners</title>
<link rel="stylesheet" href="https://fonts.googleapis.com/css2?family=Michroma&family=Montserrat:wght@600;700&family=Archivo:wght@700;800;900&display=swap">
<style>
  :root {
    --gold: #f2cf1a;
    --blue: #4885ed;
    --white: #ffffff;
    --ink: #111111;
    --stage: #000000;
  }
  * { box-sizing: border-box; margin: 0; padding: 0; }
  html, body { width: 1200px; height: 1200px; overflow: hidden; background: var(--stage); }
  .stage { position: relative; width: 1200px; height: 1200px; }

  .banner {
    position: absolute;
    left: 34px;
    width: 1132px;
    height: 258px;
    background: var(--gold);
    overflow: hidden;
  }
  .banner--first { top: 322px; }
  .banner--second { top: 607px; }

  .badge-strip {
    position: absolute;
    left: 0; top: 0;
    width: 100px; height: 258px;
  }
  .badge {
    position: absolute;
    left: 0; top: 258px;
    width: 258px; height: 100px;
    transform-origin: top left;
    transform: rotate(-90deg);
    display: flex;
    align-items: center;
    padding-left: 20px;
    font-family: "Archivo", Arial, sans-serif;
  }
  .badge__number {
    color: var(--blue);
    font-weight: 900;
    font-size: 82px;
    line-height: 1;
    letter-spacing: -3px;
    margin-right: 4px;
  }
  .badge__label { display: flex; flex-direction: column; line-height: 0.86; }
  .badge__years { color: var(--blue); font-weight: 700; font-size: 29px; }
  .badge__sub { color: var(--ink); font-weight: 700; font-size: 17px; letter-spacing: -0.3px; }

  .accent-bar {
    position: absolute;
    left: 100px; top: 0;
    width: 15px; height: 258px;
    background: var(--blue);
  }

  .photo {
    position: absolute;
    left: 115px; top: 0;
    width: 660px; height: 258px;
    clip-path: polygon(0 0, 639px 0, 539px 258px, 0 258px);
  }
  .photo--open-top { background: linear-gradient(135deg, #f3e6cf 0%, #e9d39a 45%, #d9b33a 70%, #8c8a72 100%); }
  .photo--city-car { background: linear-gradient(160deg, #2b2a24 0%, #3a3526 30%, #e9c21c 55%, #d8b31a 80%, #3b382e 100%); }

  .diagonal {
    position: absolute;
    left: 0; top: 0;
    width: 1132px; height: 258px;
    pointer-events: none;
  }

  .brand {
    position: absolute;
    right: 40px; top: 38px;
    font-family: "Michroma", "Eurostile", sans-serif;
    font-size: 30px;
    color: var(--white);
    letter-spacing: 1px;
    line-height: 1;
  }
  .tagline {
    position: absolute;
    right: 40px; top: 112px;
    text-align: right;
    font-family: "Michroma", "Eurostile", sans-serif;
  }
  .tagline__lead {
    display: block;
    color: var(--white);
    font-size: 17px;
    letter-spacing: 4px;
    margin-right: -4px;
  }
  .tagline__key {
    display: block;
    margin-top: 8px;
    color: var(--blue);
    font-size: 22px;
    letter-spacing: 4.5px;
    margin-right: -4.5px;
    font-weight: 700;
  }
  .cta {
    position: absolute;
    left: 831px; top: 200px;
    width: 263px; height: 32px;
    background: var(--blue);
    color: var(--white);
    font-family: "Montserrat", Arial, sans-serif;
    font-weight: 600;
    font-size: 14px;
    letter-spacing: 1.8px;
    display: flex; align-items: center; justify-content: center;
    text-decoration: none;
  }
</style>
</head>
<body>
<main class="stage">

  <section class="banner banner--first">
    <div class="badge-strip">
      <div class="badge">
        <span class="badge__number">25</span>
        <span class="badge__label">
          <span class="badge__years">years</span>
          <span class="badge__sub">of customer<br>satisfaction</span>
        </span>
      </div>
    </div>
    <div class="accent-bar"></div>
    <div class="photo photo--open-top" role="img" aria-label="Happy woman in a yellow shirt standing in a convertible with arms spread wide at sunset"></div>
    <svg class="diagonal" viewBox="0 0 1132 258" aria-hidden="true">
      <polygon points="754,0 768,0 670,258 654,258" fill="#4885ed"/>
    </svg>
    <div class="brand">COILHAUS</div>
    <p class="tagline">
      <span class="tagline__lead">Get it Done Right by</span>
      <span class="tagline__key">SPECIALIST</span>
    </p>
    <a class="cta" href="#">MAKE AN APPOINTMENT</a>
  </section>

  <section class="banner banner--second">
    <div class="badge-strip">
      <div class="badge">
        <span class="badge__number">25</span>
        <span class="badge__label">
          <span class="badge__years">years</span>
          <span class="badge__sub">of customer<br>satisfaction</span>
        </span>
      </div>
    </div>
    <div class="accent-bar"></div>
    <div class="photo photo--city-car" role="img" aria-label="Smiling woman posing beside a yellow compact car on a city street"></div>
    <svg class="diagonal" viewBox="0 0 1132 258" aria-hidden="true">
      <polygon points="754,0 768,0 670,258 654,258" fill="#4885ed"/>
    </svg>
    <div class="brand">COILHAUS</div>
    <p class="tagline">
      <span class="tagline__lead">Get it Done Right by</span>
      <span class="tagline__key">SPECIALIST</span>
    </p>
    <a class="cta" href="#">MAKE AN APPOINTMENT</a>
  </section>

</main>
</body>
</html>
```